Advanced Therapeutic Massage Therapist

I need a business card advertising my massage services as an advanced therapeutic massage therapist. I offer advanced therapeutic massage, swedish and deep tissue. I want to create a simple, professional and feminine card. I like bright colours and creativity.

I prefer a bold and experimental approach rather than something status-quo. A card to suggest therapeutic healing through dynamic massage. Motifs, shapes or layout which suggest movement and flow.
Updates

Target Market(s)

Everybody!

Industry/Entity Type

Health And Wellness

Contact Information for Business Card

The card should include:
My name, logo, services offered and my contact details.

Sláine Dunleavy
Massage Therapist

- Swedish - Deep Tissue - Advanced Therapeutic

Phone: (+353) 87 216 4093
Email: regenerate@slainedunleavy-example.com
Website: www.slainedunlevy-example.com

Font styles to use
Serif
Sans Serif
Decorative
Script

Colors

Designer to choose colors to be used in the design.

Requirements
Must have
• An example may contain something like this, yet concise:
• "Sláine Dunleavy
• Massage Therapist
• - Swedish - Deep Tissue - Advanced Therapeutic"
Nice to have
• This sentence is optional:
• Imagery such as a logo or symbol. I have attached a file containing a logo I had produced however the name is incorrect now as it is "Sláine" not "Nelly". It could be edited to change it to Sláine.
• I have sent the file as .psd .jpg. .pdf and .png
• I like when the card conveys energy, movement, pressure points, flow etc.
• I just like the designer to follow their own style and ideas. I like bright colours but must have a lot of a base colour to offset it. I really prefer them to follow their own inspiration. That is my preference.
Should not have
• Pine trees, non-native trees to Britain and Ireland, exotic flowers or animals that are not native to Britain and Ireland.
• I don't like brown as the background colour of the card.
• The cars shouldn't look like a wedding invitation i.e too many floral type designs.

```html
<!DOCTYPE html>
<html lang="en">
<head>
<meta charset="utf-8">
<title>Sláine Dunleavy – Massage Therapist business card</title>
<link rel="stylesheet" href="https://fonts.googleapis.com/css2?family=Kaushan+Script&family=Open+Sans:wght@400&family=Parisienne&display=swap">
<style>
  :root {
    --stage: #ecebe9;
    --paper: #ffffff;
    --ink: #2b2b2b;
    --bronze: #b06f28;
    --night: #111111;
    --seafoam: #b2d0c6;
    --mint-text: #c9ece0;
    --emblem-light: #bfe3dc;
    --emblem-deep: #8cc8bd;
    --emblem-gold: #c9962f;
  }
  * { margin: 0; padding: 0; box-sizing: border-box; }
  html, body { width: 1200px; height: 900px; overflow: hidden; }
  body { background: var(--stage); position: relative; font-family: "Open Sans", Arial, sans-serif; }

  .card { position: absolute; overflow: hidden; }
  .card-front { left: 78px; top: 35px; width: 588px; height: 362px; background: var(--paper); }
  .card-back { left: 388px; top: 505px; width: 567px; height: 352px; background: var(--night); }

  .band { position: absolute; left: 0; right: 0; }
  .card-front .band { top: 65px; height: 97px; background: var(--bronze); }
  .card-back .band { top: 63px; height: 94px; background: var(--seafoam); }

  .emblem-seat { position: absolute; border-radius: 50%; }
  .card-front .emblem-seat { left: 193px; top: 10px; width: 204px; height: 204px; background: var(--paper); }
  .card-back .emblem-seat { left: 187px; top: 10px; width: 194px; height: 194px; background: var(--night); }

  .emblem { position: absolute; border-radius: 50%;
    background: radial-gradient(circle at 45% 40%, var(--emblem-light) 0%, var(--emblem-deep) 75%, var(--emblem-gold) 100%);
    border: 2px solid var(--emblem-gold); }
  .card-front .emblem { left: 207px; top: 24px; width: 176px; height: 176px; }
  .card-back .emblem { left: 202px; top: 25px; width: 164px; height: 164px; }

  .front-text { position: absolute; left: 0; right: 0; top: 203px; text-align: center; color: var(--ink); }
  .holder-name { font-family: "Kaushan Script", cursive; font-weight: 400; color: var(--bronze); font-size: 33px; line-height: 40px; }
  .holder-role { font-size: 16px; line-height: 22px; margin-top: -3px; }
  .contact { margin-top: 7px; font-size: 15.5px; line-height: 22px; }
  .services { list-style: none; display: flex; justify-content: center; gap: 14px; margin-top: 6px; font-size: 15.5px; line-height: 22px; }
  .services li::before { content: ""; display: inline-block; width: 7px; height: 7px; border-radius: 50%; background: var(--bronze); margin-right: 6px; vertical-align: middle; position: relative; top: -2px; }

  .tagline { position: absolute; left: 0; right: 0; top: 256px; text-align: center; font-family: "Parisienne", cursive; color: var(--mint-text); font-size: 26px; line-height: 32px; letter-spacing: 0.6px; }
</style>
</head>
<body>
  <section class="card card-front" aria-label="Business card front">
    <div class="band"></div>
    <div class="emblem-seat"></div>
    <div class="emblem" role="img" aria-label="Round emblem of a gilded tree of life on a soft seafoam wash"></div>
    <div class="front-text">
      <h1 class="holder-name">Sláine Dunleavy</h1>
      <p class="holder-role">Massage Therapist</p>
      <p class="contact">(+353) 87 216 4093<br>slainemassage@example.com</p>
      <ul class="services">
        <li>Swedish</li>
        <li>Deep Tissue</li>
        <li>Advanced Therapeutic</li>
      </ul>
    </div>
  </section>

  <section class="card card-back" aria-label="Business card back">
    <div class="band"></div>
    <div class="emblem-seat"></div>
    <div class="emblem" role="img" aria-label="Round emblem of a gilded tree of life on a soft seafoam wash"></div>
    <p class="tagline">Fully qualified specialising in<br>advanced therapeutic and deep tissue massage</p>
  </section>
</body>
</html>
```